Before the kettle boils, pocast with content in its majority of technology

Page dedicated to a pocast with content in its majority of technology. The page also contains the chapters of the podcast (pluggin vocalink) will also contain news. Preferably Worpress. There is already a very basic page with a simple theme, the logo and little more, I would like something more professional. Www.lamparadebolsillo.com The logo does not want to change.

Target Market(s)

Anyone

Colors

Designer to choose colors to be used in the design.

Requirements
Must have
• You can put the vocalink pluggin with the podcast chapters

```html
<!DOCTYPE html>
<html lang="es">
<head>
<meta charset="utf-8">
<title>Before the kettle boils · Podcast de tecnología</title>
<link href="https://fonts.googleapis.com/css2?family=Lato:wght@400;700;900&family=Montserrat:wght@600;700;800&family=Open+Sans:wght@400;600&display=swap" rel="stylesheet">
<style>
:root{
  --orange:#f7901e;
  --orange-deep:#f26b1d;
  --ink:#1f1f1f;
  --dark:#231f20;
  --grey:#666;
  --line:#d8d8d8;
  --blue:#3a78b8;
  --white:#fff;
}
*{box-sizing:border-box;margin:0;padding:0}
html,body{width:1200px;height:3557px;overflow:hidden}
body{position:relative;background:var(--white);font-family:"Lato",sans-serif;color:var(--ink)}
.abs{position:absolute}

/* header */
.site-header{position:absolute;left:0;top:0;width:1200px;height:111px;background:var(--dark);z-index:2}
.brand{position:absolute;left:118px;top:18px;display:flex;align-items:center;gap:14px}
.brand-dot{width:62px;height:62px;border-radius:50%;background:var(--orange)}
.brand-name{font-family:"Montserrat",sans-serif;font-weight:800;font-size:23px;color:var(--orange);letter-spacing:.5px;text-transform:uppercase;line-height:1}
.brand-tag{font-family:"Lato",sans-serif;font-size:18px;color:var(--white);letter-spacing:1px;margin-top:6px}
.main-nav{position:absolute;right:118px;top:44px;display:flex;gap:44px;font-family:"Montserrat",sans-serif;font-weight:600;font-size:15px;color:var(--white)}
.main-nav .active{color:var(--orange)}

/* hero */
.hero{position:absolute;left:0;top:111px;width:1200px;height:565px;background:linear-gradient(100deg,#3a2f2a 0%,#6b5548 35%,#2d3440 62%,#44607e 80%,#2a2c33 100%)}
.hero-play{position:absolute;left:548px;top:159px;width:114px;height:114px;border-radius:50%;background:var(--white)}
.hero-play svg{position:absolute;left:40px;top:32px}
.hero-title{position:absolute;left:0;width:1200px;text-align:center;font-family:"Montserrat",sans-serif;font-weight:800;color:var(--white);text-transform:uppercase}
.hero-title.l1{top:296px;font-size:42px;letter-spacing:1px;left:-60px}
.hero-title.l2{top:356px;font-size:32px;left:-40px}

/* section title */
.section-title{position:absolute;left:118px;top:734px;font-family:"Lato",sans-serif;font-weight:400;font-size:28px;letter-spacing:.5px}

/* post cards */
.post-card{position:absolute;left:116px;width:669px;height:430px;border:1px solid var(--line);background:var(--white)}
.post-thumb{position:absolute;left:21px;top:28px;width:314px;height:207px}
.post-body{position:absolute;left:349px;top:30px;width:300px}
.post-title{font-family:"Lato",sans-serif;font-weight:700;font-size:20px;color:var(--orange);line-height:1.25;margin-bottom:8px}
.post-excerpt{font-family:"Open Sans",sans-serif;font-size:12px;line-height:18px;color:var(--grey)}
.post-more{font-family:"Open Sans",sans-serif;font-size:11.5px;font-weight:600;color:var(--ink);margin-top:10px}
.post-date{font-family:"Open Sans",sans-serif;font-size:11.5px;color:var(--blue);margin-top:4px}
.player{position:absolute;left:0;top:262px;width:669px;height:168px}
.player-title{position:absolute;left:24px;top:2px;font-family:"Lato",sans-serif;font-weight:700;font-size:17px}
.player-btn{position:absolute;left:24px;top:38px;width:58px;height:58px;border:3px solid var(--ink);border-radius:50%}
.player-btn svg{position:absolute;left:19px;top:14px}
.player-wave{position:absolute;left:102px;top:22px;width:505px;height:96px}
.player-time{position:absolute;top:88px;font-family:"Open Sans",sans-serif;font-size:14px;color:var(--ink)}
.player-time.start{left:104px}
.player-time.end{right:18px}
.player-actions{position:absolute;right:36px;top:12px;display:flex;gap:22px}
.share-row{position:absolute;left:104px;top:114px;display:flex;gap:6px}
.share-row span{width:23px;height:23px;border:1.5px solid #888;border-radius:50%}

/* pagination */
.pager{position:absolute;left:337px;top:3084px;display:flex;gap:6px}
.pager span{width:28px;height:28px;border:1px solid #c8c8c8;background:#f2f2f2;font-family:"Open Sans",sans-serif;font-size:13px;color:#555;display:flex;align-items:center;justify-content:center}
.pager .current{background:var(--orange);border-color:var(--orange);color:var(--white)}

/* sidebar */
.side-box{position:absolute;left:821px;width:261px}
.about-box{top:759px;height:380px;background:linear-gradient(180deg,var(--orange) 0%,var(--orange-deep) 100%);text-align:center;color:var(--white);padding:36px 28px 0}
.about-box h3{font-family:"Lato",sans-serif;font-weight:400;font-size:27px;letter-spacing:1px;margin-bottom:20px}
.about-box p{font-family:"Open Sans",sans-serif;font-size:12px;line-height:19px;color:#fff5e6}
.btn-outline{display:inline-block;font-family:"Open Sans",sans-serif;font-size:12.5px;font-weight:600;padding:8px 30px;border:2px solid currentColor}
.about-box .btn-outline{position:absolute;left:59px;bottom:38px;color:var(--white)}
.recent-box{top:1160px;height:353px;background:var(--white);box-shadow:0 2px 10px rgba(0,0,0,.16);text-align:center;padding-top:30px}
.recent-box h3{font-family:"Lato",sans-serif;font-weight:400;font-size:21px;margin-bottom:22px}
.recent-box li{list-style:none;font-family:"Open Sans",sans-serif;font-size:12px;line-height:17px;color:var(--ink);margin:0 auto 12px;width:160px}
.recent-box .btn-outline{position:absolute;left:68px;bottom:34px;color:var(--ink)}
.top-box{top:1537px;height:432px;background:var(--white);box-shadow:0 2px 10px rgba(0,0,0,.16)}
.top-head{height:48px;background:#111;color:var(--white);font-family:"Lato",sans-serif;font-size:21px;padding:11px 0 0 34px}
.top-item{position:absolute;left:22px;width:225px;height:100px}
.top-item .thumb{position:absolute;left:0;top:0;width:64px;height:64px;border-radius:50%}
.top-item .txt{position:absolute;left:76px;top:0;width:150px}
.top-item h4{font-family:"Lato",sans-serif;font-weight:700;font-size:14px;color:var(--orange);margin-bottom:4px}
.top-item p{font-family:"Open Sans",sans-serif;font-size:11px;line-height:15px;color:#999}
.top-item b{display:block;font-family:"Open Sans",sans-serif;font-size:11px;font-weight:600;margin-top:4px}
.ad{position:absolute;left:817px;width:258px;height:209px}

/* footer */
.site-footer{position:absolute;left:0;top:3190px;width:1200px;height:367px;background:var(--dark);color:var(--white)}
.foot-col{position:absolute;top:68px}
.foot-col h4{font-family:"Lato",sans-serif;font-weight:400;font-size:18px;margin-bottom:18px}
.foot-col li{list-style:none;font-family:"Open Sans",sans-serif;font-size:13.5px;line-height:26px;color:#ddd}
.field{width:263px;height:34px;border:1px solid #888;margin-bottom:12px;font-family:"Open Sans",sans-serif;font-size:12px;padding:9px 12px;color:#eee}
.submit{display:inline-block;background:var(--orange);font-family:"Open Sans",sans-serif;font-size:13px;font-weight:600;padding:10px 38px;margin-top:10px}
.social{display:flex;gap:6px}
.social span{width:28px;height:28px;border:2px solid var(--white);border-radius:50%}
.foot-rule{position:absolute;left:130px;top:290px;width:960px;height:1px;background:#555}
.copyright{position:absolute;left:0;top:317px;width:1200px;text-align:center;font-family:"Open Sans",sans-serif;font-size:12px;color:#aaa}
</style>
</head>
<body>

<svg width="0" height="0" style="position:absolute">
  <defs>
    <symbol id="wave" viewBox="0 0 200 40" preserveAspectRatio="none">
      <path stroke="#f7901e" stroke-width="1.6" fill="none" d="M2 17v6M4.9 15v10M7.8 16v8M10.7 12v16M13.6 14v12M16.5 10v20M19.4 13v14M22.3 8v24M25.2 11v18M28.1 6v28M31 9v22M33.9 12v16M36.8 7v26M39.7 4v32M42.6 8v24M45.5 11v18M48.4 5v30M51.3 2v36M54.2 7v26M57.1 10v20M60 13v14M62.9 9v22M65.8 6v28M68.7 3v34M71.6 8v24M74.5 12v16M77.4 15v10M80.3 11v18M83.2 7v26M86.1 4v32M89 1v38M91.9 6v28M94.8 10v20M97.7 13v14M100.6 8v24M103.5 5v30M106.4 9v22M109.3 12v16M112.2 14v12M115.1 10v20M118 7v26M120.9 3v34M123.8 6v28M126.7 11v18M129.6 14v12M132.5 16v8M135.4 12v16M138.3 9v22M141.2 5v30M144.1 8v24M147 11v18M149.9 7v26M152.8 4v32M155.7 9v22M158.6 13v14M161.5 15v10M164.4 11v18M167.3 8v24M170.2 12v16M173.1 14v12M176 16v8M178.9 13v14M181.8 15v10M184.7 17v6M187.6 14v12M190.5 16v8M193.4 17v6M196.3 18v4"/>
    </symbol>
    <symbol id="heart" viewBox="0 0 16 14"><path d="M8 13 1.5 6.5A3.5 3.5 0 0 1 8 2.5a3.5 3.5 0 0 1 6.5 4Z" fill="#aaa"/></symbol>
    <symbol id="bubble" viewBox="0 0 16 14"><path d="M2 1h12v8H6l-3 3V9H2Z" fill="#aaa"/></symbol>
    <symbol id="share" viewBox="0 0 16 14"><g fill="#aaa"><circle cx="3" cy="7" r="2.2"/><circle cx="13" cy="2.5" r="2.2"/><circle cx="13" cy="11.5" r="2.2"/></g><path d="M3 7 13 2.5M3 7l10 4.5" stroke="#aaa" stroke-width="1.3"/></symbol>
    <symbol id="tri" viewBox="0 0 20 26"><path d="M0 0 20 13 0 26Z" fill="#1f1f1f"/></symbol>
  </defs>
</svg>

<header class="site-header">
  <div class="brand">
    <div class="brand-dot"></div>
    <div>
      <div class="brand-name">Before the kettle boils</div>
      <div class="brand-tag">PODCAST DE TECNOLOGÍA</div>
    </div>
  </div>
  <nav class="main-nav">
    <span class="active">HOME</span><span>ABOUT</span><span>BLOGS</span><span>PODCAST</span><span>CONTACT</span>
  </nav>
</header>

<section class="hero" role="img" aria-label="Studio photo: microphone with pop filter in front of a mixing desk and monitor">
  <div class="hero-play"><svg width="40" height="50" viewBox="0 0 20 26"><use href="#tri"/></svg></div>
  <h1 class="hero-title l1">Maecenas aliquet velit vel</h1>
  <h2 class="hero-title l2">Neque metus malesu</h2>
</section>

<h2 class="section-title">LATEST BLOGS</h2>

<!-- post 1 -->
<article class="post-card" style="top:792px">
  <div class="post-thumb" role="img" aria-label="Close-up photo of a studio microphone" style="background:linear-gradient(135deg,#2a2a2a,#6a6a6a 55%,#1c1c1c)"></div>
  <div class="post-body">
    <h3 class="post-title">Cambio de logo</h3>
    <p class="post-excerpt">¿Salta a la vista no?, pues sí, renovamos diseño del logo y algo en la web.<br>Aquí los cambios irán poco a poco pero procuraré dejar todo lo que quiero modificar hecho en una semana como mucho, todo dependerá del tiempo que le pueda dedicar aunque</p>
    <p class="post-more">READ MORE</p>
    <p class="post-date">19 MAY, 2017 DE MARLEN</p>
  </div>
  <div class="player">
    <div class="player-title">Un anuncio y una prueba</div>
    <div class="player-actions"><svg width="14" height="13"><use href="#heart"/></svg><svg width="14" height="13"><use href="#bubble"/></svg><svg width="14" height="13"><use href="#share"/></svg></div>
    <div class="player-btn"><svg width="20" height="26"><use href="#tri"/></svg></div>
    <svg class="player-wave"><use href="#wave"/></svg>
    <span class="player-time start">00:00</span><span class="player-time end">08:00</span>
    <div class="share-row"><span></span><span></span><span></span><span></span><span></span><span></span><span></span></div>
  </div>
</article>

<!-- post 2 -->
<article class="post-card" style="top:1243px">
  <div class="post-thumb" role="img" aria-label="Photo of a young woman looking at her phone" style="background:linear-gradient(135deg,#3b3438,#8a5a5e 50%,#2b2a2e)"></div>
  <div class="post-body">
    <h3 class="post-title">¿Te gustan las series?¿Conoces velocine.tv?</h3>
    <p class="post-excerpt">Hoy capítulo dedicado a los amantes de las series y las películas. Se trata del servicio de vídeo en streaming de la web velocine.tv portal dedicado al aprendizaje de inglés mediante el método de ver películas y series en inglés con subtítulos.</p>
    <p class="post-more">READ MORE</p>
    <p class="post-date">19 MAY, 2017 DE MARLEN</p>
  </div>
  <div class="player">
    <div class="player-title">¿Te gustan las series?¿Conoces velocine.tv?</div>
    <div class="player-actions"><svg width="14" height="13"><use href="#heart"/></svg><svg width="14" height="13"><use href="#bubble"/></svg><svg width="14" height="13"><use href="#share"/></svg></div>
    <div class="player-btn"><svg width="20" height="26"><use href="#tri"/></svg></div>
    <svg class="player-wave"><use href="#wave"/></svg>
    <span class="player-time start">00:00</span><span class="player-time end">08:00</span>
    <div class="share-row"><span></span><span></span><span></span><span></span><span></span><span></span><span></span></div>
  </div>
</article>

<!-- post 3 -->
<article class="post-card" style="top:1694px">
  <div class="post-thumb" role="img" aria-label="Photo of a recording studio with screens and a mixing console" style="background:linear-gradient(135deg,#1e2a4a,#4d6fa8 45%,#7a3b32 80%,#221c1c)"></div>
  <div class="post-body">
    <h3 class="post-title">Un anuncio y una prueba</h3>
    <p class="post-excerpt">¿Salta a la vista no?, pues sí, renovamos diseño del logo y algo en la web.<br>Aquí los cambios irán poco a poco pero procuraré dejar todo lo que quiero modificar hecho en una semana como mucho, todo dependerá del tiempo que le pueda dedicar aunque</p>
    <p class="post-more">READ MORE</p>
    <p class="post-date">19 MAY, 2017 DE MARLEN</p>
  </div>
  <div class="player">
    <div class="player-title">Un anuncio y una prueba</div>
    <div class="player-actions"><svg width="14" height="13"><use href="#heart"/></svg><svg width="14" height="13"><use href="#bubble"/></svg><svg width="14" height="13"><use href="#share"/></svg></div>
    <div class="player-btn"><svg width="20" height="26"><use href="#tri"/></svg></div>
    <svg class="player-wave"><use href="#wave"/></svg>
    <span class="player-time start">00:00</span><span class="player-time end">08:00</span>
    <div class="share-row"><span></span><span></span><span></span><span></span><span></span><span></span><span></span></div>
  </div>
</article>

<!-- post 4 -->
<article class="post-card" style="top:2147px">
  <div class="post-thumb" role="img" aria-label="Photo of a smiling woman with headphones in a city" style="background:linear-gradient(135deg,#9db4cc,#d8dfe6 45%,#b2473e 75%,#5a6b80)"></div>
  <div class="post-body">
    <h3 class="post-title">Seguridad en tu Mail</h3>
    <p class="post-excerpt">Hoy poco más que decir por aquí de lo dicho en el podcast. Para aquellos que necesiten un punto más de seguridad en el correo electrónico está VaultMail. Planes gratuitos y de pago, codificación, mensajes que se pueden auto destruir, etc</p>
    <p class="post-more">READ MORE</p>
    <p class="post-date">19 MAY, 2017 DE MARLEN</p>
  </div>
  <div class="player">
    <div class="player-title">Seguridad en tu Mail</div>
    <div class="player-actions"><svg width="14" height="13"><use href="#heart"/></svg><svg width="14" height="13"><use href="#bubble"/></svg><svg width="14" height="13"><use href="#share"/></svg></div>
    <div class="player-btn"><svg width="20" height="26"><use href="#tri"/></svg></div>
    <svg class="player-wave"><use href="#wave"/></svg>
    <span class="player-time start">00:00</span><span class="player-time end">08:00</span>
    <div class="share-row"><span></span><span></span><span></span><span></span><span></span><span></span><span></span></div>
  </div>
</article>

<!-- post 5 -->
<article class="post-card" style="top:2595px">
  <div class="post-thumb" role="img" aria-label="Photo of a vintage microphone on a dark background" style="background:linear-gradient(135deg,#1d2733,#55606b 50%,#2e2a26)"></div>
  <div class="post-body">
    <h3 class="post-title">Koru Tab2, calidad precio insuperable</h3>
    <p class="post-excerpt">Con un poco de retraso publicamos el post del podcast de la tableta de Koru. Tableta que como viene siendo habitual de la marca, da mucho más de lo que cuesta.</p>
    <p class="post-more">READ MORE</p>
    <p class="post-date">19 MAY, 2017 DE MARLEN</p>
  </div>
  <div class="player">
    <div class="player-title">Koru Tab2, calidad</div>
    <div class="player-actions"><svg width="14" height="13"><use href="#heart"/></svg><svg width="14" height="13"><use href="#bubble"/></svg><svg width="14" height="13"><use href="#share"/></svg></div>
    <div class="player-btn"><svg width="20" height="26"><use href="#tri"/></svg></div>
    <svg class="player-wave"><use href="#wave"/></svg>
    <span class="player-time start">00:00</span><span class="player-time end">08:00</span>
    <div class="share-row"><span></span><span></span><span></span><span></span><span></span><span></span><span></span></div>
  </div>
</article>

<nav class="pager">
  <span>‹</span><span class="current">1</span><span>2</span><span>3</span><span>4</span><span>5</span><span>6</span><span>›</span>
</nav>

<!-- sidebar -->
<aside>
  <div class="side-box about-box">
    <h3>ABOUT US</h3>
    <p>Maecenas aliquet velit vel turpis. Mauris neque metus malesuada nec ultricies sit amet porttitor mattis enim in massa. Nam<br>Interdum vel blandit sed nulla in ullamcorper est eget tempor cursus neque mi consectetur mi a ultricies massa est sed mi Class aptent taciti sociosqu ad litora to</p>
    <span class="btn-outline">READ MORE</span>
  </div>

  <div class="side-box recent-box">
    <h3>Recent Posts</h3>
    <ul>
      <li>Cambio de logo</li>
      <li>¿Te gustan las series?¿Conoces velocine.tv?</li>
      <li>Un anuncio y una prueba</li>
      <li>Seguridad en tu Mail</li>
      <li>Koru Tab2, calidad precio insuperable</li>
    </ul>
    <span class="btn-outline">READ MORE</span>
  </div>

  <div class="side-box top-box">
    <div class="top-head">Top Blogs</div>
    <div class="top-item" style="top:78px">
      <div class="thumb" role="img" aria-label="Round photo of a person at a desk" style="background:linear-gradient(135deg,#5b4a3e,#b89a80)"></div>
      <div class="txt"><h4>Aeque consectetuer</h4><p>Praesent elementum elit at tellus Curabitur metus ipsum luctus</p><b>READ MORE</b></div>
    </div>
    <div class="top-item" style="top:200px">
      <div class="thumb" role="img" aria-label="Round photo of a person with headphones" style="background:linear-gradient(135deg,#8a6a5a,#d9b9a0)"></div>
      <div class="txt"><h4>Ut nisi erat ferm</h4><p>Praesent elementum elit at tellus Curabitur</p><b>READ MORE</b></div>
    </div>
    <div class="top-item" style="top:316px">
      <div class="thumb" role="img" aria-label="Round photo of a studio scene" style="background:linear-gradient(135deg,#3a2424,#a13a3a)"></div>
      <div class="txt"><h4>Curabitur iaculis</h4><p>Praesent elementum elit at tellus Curabitur</p><b>READ MORE</b></div>
    </div>
  </div>

  <div class="ad" style="top:1997px;background:linear-gradient(135deg,#ffd800,#f5c400)" role="img" aria-label="Advertisement banner for a mobile phone plan"></div>
  <div class="ad" style="top:2230px;background:linear-gradient(180deg,#e23a2e,#b81f1f)" role="img" aria-label="Advertisement banner for a cloud messaging service"></div>
  <div class="ad" style="top:2460px;background:linear-gradient(180deg,#1d5fa8,#dfe6ee 70%,#ffffff)" role="img" aria-label="Advertisement banner for a car"></div>
  <div class="ad" style="top:2690px;background:linear-gradient(135deg,#050505,#2a2a2a 60%,#111)" role="img" aria-label="Advertisement banner for a razor"></div>
  <div class="ad" style="top:2918px;background:linear-gradient(180deg,#3fa9e0,#1f86c6)" role="img" aria-label="Advertisement banner for a website builder"></div>
</aside>

<footer class="site-footer">
  <div class="foot-col" style="left:142px">
    <h4>Quick Links</h4>
    <ul><li>Home</li><li>About Us</li><li>Our Blogs</li><li>Podcast</li></ul>
  </div>
  <div class="foot-col" style="left:370px">
    <h4>Resources</h4>
    <ul><li>Top Rated</li><li>News</li><li>Contact Us</li></ul>
  </div>
  <div class="foot-col" style="left:591px">
    <h4>Quick Contact</h4>
    <div class="field">Name</div>
    <div class="field">Email address</div>
    <span class="submit">SUBMIT</span>
  </div>
  <div class="foot-col" style="left:908px">
    <h4>Stay in Touch</h4>
    <div class="social"><span></span><span></span><span></span><span></span></div>
  </div>
  <div class="foot-rule"></div>
  <p class="copyright">© 2017 Company Name &nbsp;All right reserved &nbsp;Term of Use</p>
</footer>

</body>
</html>
```